Business Card for a Jewellery Brand

Business card for an upscale jewellery brand. Attached is the brand logo and icon and color board. I am looking for two card versions: one for the founder and one is generic. The card should be elegant and convey upscale and premium feel. I am open to both square and rectangle card shapes.

Industry/Entity Type

Jewelry

Contact Information for Business Card

Two cards: (1) Sunela Parvaniya (Founder) (2) General
(1) Sunela Parvaniya card should have Name: Sunela Parvaniya, Title: Founder Email id: sunela@quiremo.com.au. Phone no: +61452913307
(2) Generic card should have Email id: info@quiremo.com.au. Phone no: +61436207518

Requirements
Must have
• Workmark
• ICON
• Phone no
• Email ID
• ABN: 58219740312 (Note: ABN is Business number in Australia)
• Website: www.quiremo.com.au
• Instagram: quiremo_jewellery
• Facebook: @quiremojewellery
Nice to have
• Tagline

```html
<!DOCTYPE html>
<html lang="en">
<head>
<meta charset="utf-8">
<title>Quiremo Business Cards</title>
<link href="https://fonts.googleapis.com/css2?family=Lato:wght@400;700&display=swap" rel="stylesheet">
<style>
  :root {
    --rose: #e3958f;
    --rose-pale: #fbe3df;
    --white: #ffffff;
    --ground: #2e2e30;
  }
  * { margin: 0; padding: 0; box-sizing: border-box; }
  html, body { width: 1200px; height: 880px; overflow: hidden; }
  body {
    background: var(--ground);
    font-family: "Lato", sans-serif;
    position: relative;
  }
  .card {
    position: absolute;
    width: 600px;
    height: 343px;
    border-radius: 22px;
    overflow: hidden;
  }
  /* Back of card */
  .card-back {
    left: 90px; top: 90px;
    background: var(--rose);
    color: var(--white);
  }
  .card-back .brand {
    position: absolute;
    left: 0; right: 0; top: 118px;
    display: flex; align-items: center; justify-content: center; gap: 16px;
  }
  .brand-dot {
    width: 22px; height: 22px; border-radius: 50%;
    background: currentColor;
  }
  .card-back .brand-name {
    font-size: 44px; font-weight: 400; letter-spacing: 12px;
  }
  .card-back .website {
    position: absolute; left: 0; right: 0; top: 228px;
    text-align: center; font-size: 17px; letter-spacing: 3px;
  }
  /* Front of card */
  .card-front {
    left: 510px; top: 447px;
    background: var(--white);
    color: var(--rose);
  }
  .card-front .wave { position: absolute; inset: 0; }
  .holder {
    position: absolute; right: 34px; top: 30px; text-align: right;
  }
  .holder-name { font-size: 22px; font-weight: 700; letter-spacing: .3px; }
  .holder-title { font-size: 15px; margin-top: 1px; }
  .wordmark {
    position: absolute; left: 44px; top: 106px;
    display: flex; align-items: center; gap: 12px;
  }
  .wordmark .brand-dot { width: 17px; height: 17px; }
  .wordmark .brand-name { font-size: 34px; letter-spacing: 8px; }
  .abn {
    position: absolute; left: 48px; top: 164px;
    font-size: 16px; letter-spacing: 1px;
  }
  .contacts {
    position: absolute; right: 30px; top: 150px;
    list-style: none; color: var(--white);
    font-size: 14px; line-height: 20px; text-align: right;
  }
  .contacts li { display: flex; justify-content: flex-end; align-items: center; gap: 8px; }
  .icon {
    width: 16px; height: 16px; border-radius: 50%;
    background: var(--white); flex: none;
    display: inline-flex; align-items: center; justify-content: center;
  }
  .icon svg { width: 10px; height: 10px; }
</style>
</head>
<body>

  <section class="card card-back">
    <div class="brand">
      <span class="brand-dot"></span>
      <span class="brand-name">QUIREMO</span>
    </div>
    <p class="website">www.quiremo.com.au</p>
  </section>

  <section class="card card-front">
    <svg class="wave" viewBox="0 0 600 343" width="600" height="343" aria-hidden="true">
      <path d="M0,298 C130,292 220,262 260,212 C240,262 170,314 0,324 Z" fill="var(--rose-pale)"/>
      <path d="M0,330 C160,326 240,282 272,222 C250,300 190,343 130,343 L0,343 Z" fill="var(--rose)"/>
      <path d="M600,96 C500,96 420,110 372,150 C330,190 300,290 210,343 L600,343 Z" fill="var(--rose)"/>
      <path d="M540,80 C450,86 380,100 345,140 C310,190 280,300 180,338" fill="none" stroke="var(--rose)" stroke-width="6" stroke-linecap="round"/>
    </svg>

    <div class="holder">
      <p class="holder-name">Sunela Parvaniya</p>
      <p class="holder-title">Founder</p>
    </div>

    <div class="wordmark">
      <span class="brand-dot"></span>
      <span class="brand-name">QUIREMO</span>
    </div>
    <p class="abn">ABN: 58219740312</p>

    <ul class="contacts">
      <li>+61452913307
        <span class="icon"><svg viewBox="0 0 10 10"><path d="M2 1 L4 1 L4.6 3 L3.4 3.8 C4 5 5 6 6.2 6.6 L7 5.4 L9 6 L9 8 C5 9 1 5 2 1 Z" fill="var(--rose)"/></svg></span>
      </li>
      <li>sunela@quiremo.com.au
        <span class="icon"><svg viewBox="0 0 10 10"><rect x="1" y="2.5" width="8" height="5.5" fill="var(--rose)"/><path d="M1 2.5 L5 5.5 L9 2.5" fill="none" stroke="var(--white)" stroke-width="0.8"/></svg></span>
      </li>
      <li>quiremo_jewellery <span class="icon"></span></li>
      <li>@quiremojewellery <span class="icon"></span></li>
      <li>www.quiremo.com.au
        <span class="icon"><svg viewBox="0 0 10 10"><circle cx="5" cy="5" r="3.8" fill="none" stroke="var(--rose)" stroke-width="1"/><ellipse cx="5" cy="5" rx="1.6" ry="3.8" fill="none" stroke="var(--rose)" stroke-width="0.8"/><line x1="1.2" y1="5" x2="8.8" y2="5" stroke="var(--rose)" stroke-width="0.8"/></svg></span>
      </li>
    </ul>
  </section>

</body>
</html>
```